SANDWICH SKILLET DESIGN (Packaging)

We require a skillet (sandwich box) designed I have uploaded a similar one we have already
I have uploaded the logo to be placed on the skillet
( BRIGHT MEADOW DELI HAWKS LTD)
we would like a sandwich skillet which has a white background and maybe some veg items which maybe found in a sandwich
hope this helps

```html
<!DOCTYPE html>
<html lang="en">
<head>
<meta charset="utf-8">
<title>Bright Meadow Deli – Sandwich Skillet</title>
<link rel="stylesheet" href="https://fonts.googleapis.com/css2?family=Roboto+Condensed:wght@700&display=swap">
<style>
  :root {
    --brand-red: #94150d;
    --wood: #e6d9cb;
    --wood-deep: #d9c8b6;
    --wood-light: #efe5da;
    --dieline-grey: #efefef;
    --white: #ffffff;
  }
  html, body {
    margin: 0;
    padding: 0;
    width: 1200px;
    height: 910px;
    overflow: hidden;
    background: var(--white);
  }
  .skillet-net {
    display: block;
    width: 1200px;
    height: 910px;
  }
  .dieline-area { fill: var(--dieline-grey); }
  .brand-band { fill: var(--brand-red); }
  .badge-disc { fill: var(--white); stroke: var(--brand-red); }
  .badge-ring { fill: none; stroke: var(--brand-red); }
  .panel-text {
    font-family: "Roboto Condensed", "Arial Narrow", sans-serif;
    font-weight: 700;
    fill: var(--white);
  }
  .label-email {
    font-family: "Roboto Condensed", "Arial Narrow", sans-serif;
    font-weight: 700;
    fill: var(--brand-red);
  }
  .badge-name {
    font-family: "Roboto Condensed", "Arial Narrow", sans-serif;
    font-weight: 700;
    fill: var(--brand-red);
    text-anchor: middle;
  }
</style>
</head>
<body>
<svg class="skillet-net" viewBox="0 0 2212 1680" preserveAspectRatio="none" xmlns="http://www.w3.org/2000/svg">
  <defs>
    <linearGradient id="wood-tone" x1="0" y1="0" x2="1" y2="1">
      <stop offset="0" stop-color="var(--wood-light)"/>
      <stop offset="0.5" stop-color="var(--wood)"/>
      <stop offset="1" stop-color="var(--wood-deep)"/>
    </linearGradient>
    <linearGradient id="front-wood-tone" x1="0" y1="0" x2="0" y2="1">
      <stop offset="0" stop-color="#f1e8de"/>
      <stop offset="1" stop-color="#e4d5c5"/>
    </linearGradient>
    <radialGradient id="salad-tone" cx="0.45" cy="0.45" r="0.65">
      <stop offset="0" stop-color="#5d9a34"/>
      <stop offset="0.45" stop-color="#82b24e"/>
      <stop offset="0.75" stop-color="#c64a34"/>
      <stop offset="1" stop-color="#8fb96a" stop-opacity="0.6"/>
    </radialGradient>
    <radialGradient id="wheat-tone" cx="0.5" cy="0.5" r="0.5">
      <stop offset="0" stop-color="#c99a4e"/>
      <stop offset="1" stop-color="#d8b173" stop-opacity="0"/>
    </radialGradient>
    <radialGradient id="corn-tone" cx="0.5" cy="0.5" r="0.5">
      <stop offset="0" stop-color="#e3c52a"/>
      <stop offset="1" stop-color="#e8d04a" stop-opacity="0"/>
    </radialGradient>
    <radialGradient id="nut-tone" cx="0.5" cy="0.5" r="0.5">
      <stop offset="0" stop-color="#b88a5c"/>
      <stop offset="1" stop-color="#c49a70" stop-opacity="0"/>
    </radialGradient>
    <radialGradient id="splash-tone" cx="0.5" cy="0.5" r="0.5">
      <stop offset="0" stop-color="#ffffff"/>
      <stop offset="0.7" stop-color="#f7f5f2"/>
      <stop offset="1" stop-color="#ffffff" stop-opacity="0"/>
    </radialGradient>
    <filter id="soft-edge" x="-10%" y="-10%" width="120%" height="120%">
      <feGaussianBlur stdDeviation="9"/>
    </filter>
    <clipPath id="top-panel-clip">
      <polygon points="662,15 1290,15 1600,335 1600,1570 1450,1450 1000,1005 700,700 680,690"/>
    </clipPath>
    <clipPath id="left-panel-clip">
      <polygon points="5,710 685,710 1000,1010 1020,1590 440,1625 5,1290"/>
    </clipPath>
  </defs>

  <!-- dieline flaps -->
  <polygon class="dieline-area" role="img" aria-label="Glue flap"
           points="90,620 320,385 680,700 90,700"/>
  <polygon class="dieline-area" role="img" aria-label="Base flap"
           points="450,1640 1000,1010 1030,1010 1600,1590 1600,1650 450,1650"/>

  <!-- wood panels -->
  <polygon fill="url(#wood-tone)" role="img" aria-label="Light wood grain surface"
           points="662,15 1290,15 1600,335 1600,1570 1450,1450 1000,1005 700,700 680,690"/>
  <polygon fill="url(#wood-tone)" role="img" aria-label="Light wood grain surface"
           points="5,710 685,710 1000,1010 1020,1590 440,1625 5,1290"/>
  <path fill="url(#front-wood-tone)" role="img" aria-label="Light wood grain surface"
        d="M1600,390 Q1600,340 1650,340 L2212,340 L2212,1680 L1600,1680 Z"/>

  <!-- produce imagery -->
  <g clip-path="url(#top-panel-clip)">
    <path fill="url(#salad-tone)" filter="url(#soft-edge)" role="img"
          aria-label="Falling lettuce, cucumber slices, red onion rings, olives and tomato"
          d="M655,10 L770,10 C850,60 900,170 870,240 C825,300 740,330 748,420 C760,500 830,520 805,585 C785,640 745,690 680,695 Z"/>
    <path fill="url(#splash-tone)" role="img" aria-label="Milk splash"
          d="M790,640 C800,580 850,530 905,530 C945,545 935,600 900,640 C880,680 840,700 800,690 Z"/>
    <ellipse fill="url(#nut-tone)" role="img" aria-label="Almonds" cx="765" cy="705" rx="40" ry="30"/>
    <ellipse fill="url(#wheat-tone)" role="img" aria-label="Wheat ears" cx="1165" cy="770" rx="100" ry="55" transform="rotate(-35 1165 770)"/>
    <path fill="url(#salad-tone)" filter="url(#soft-edge)" role="img"
          aria-label="Salad with cucumber, tomato, olives, mushrooms, rocket and celery"
          d="M1100,845 C1180,760 1320,715 1440,700 C1530,715 1600,780 1600,900 C1590,1000 1525,1100 1505,1250 C1495,1330 1475,1400 1420,1405 C1340,1325 1200,1200 1030,1020 C1020,950 1050,885 1100,845 Z"/>
    <ellipse fill="url(#corn-tone)" role="img" aria-label="Sweetcorn kernels" cx="975" cy="935" rx="55" ry="35"/>
  </g>
  <g clip-path="url(#left-panel-clip)">
    <path fill="url(#salad-tone)" filter="url(#soft-edge)" role="img"
          aria-label="Tossed salad with mushrooms, tomatoes, red onion and olives"
          d="M5,705 L690,705 C600,780 560,850 500,905 C440,965 360,1050 290,1090 C220,1075 180,985 130,930 C80,870 30,800 5,745 Z"/>
  </g>

  <!-- brand band and badge -->
  <polygon class="brand-band" points="1420,152 1502,236 1150,592 1068,510"/>
  <circle class="badge-disc" cx="1097" cy="565" r="95" stroke-width="8"/>
  <circle class="badge-ring" cx="1097" cy="565" r="78" stroke-width="3"/>
  <text class="badge-name" x="1097" y="560" font-size="25">BRIGHT MEADOW</text>
  <text class="badge-name" x="1097" y="592" font-size="25">DELI</text>

  <!-- company details label -->
  <g transform="translate(900,800) rotate(42)">
    <rect class="brand-band" x="-165" y="-62" width="330" height="100"/>
    <rect fill="var(--white)" x="-165" y="38" width="330" height="34"/>
    <text class="panel-text" x="-150" y="-28" font-size="19">BRIGHT MEADOW DELI HAWKS LTD</text>
    <text class="panel-text" x="-150" y="0" font-size="19">UNIT 4 ALDER ROW HK7 2MD</text>
    <text class="label-email" x="-150" y="62" font-size="19">HELLO@BRIGHTMEADOWDELI.CO</text>
  </g>

  <!-- front panel -->
  <rect class="brand-band" x="1678" y="348" width="464" height="364"/>
  <text class="panel-text" x="1910" y="562" font-size="29" text-anchor="middle">FRESHLY HANDMADE SANDWICHES</text>

  <rect class="brand-band" x="1788" y="1440" width="232" height="80"/>
  <rect class="brand-band" x="1600" y="1505" width="612" height="175"/>
  <circle class="badge-disc" cx="1902" cy="1322" r="162" stroke-width="14"/>
  <circle class="badge-ring" cx="1902" cy="1322" r="135" stroke-width="4"/>
  <text class="badge-name" x="1902" y="1318" font-size="34">BRIGHT MEADOW</text>
  <text class="badge-name" x="1902" y="1360" font-size="34">DELI</text>

  <text class="panel-text" x="1906" y="1588" font-size="29" text-anchor="middle">EAT ON DAY OF PURCHASE</text>
  <text class="panel-text" x="1906" y="1634" font-size="29" text-anchor="middle">KEEP REFRIGERATED BELOW 5 C</text>
</svg>
</body>
</html>
```